Business Card, A4 Letter Head and DL Envelope for Brandvelle

We are looking for a design for our Business Card, A4 Letter Head and DL Envelope.

Brandvelle is a distributor of promotional products. We specialize in a range of branded promotional products, these include pens, polo shirts, key rings, drink bottles, uniforms and bags to name a few. We are experts in marketing and assist companies in choosing the right promotional product for their needs. We will predominately be an online business where customers visit our website and browse our range of promotional products and branding options.

Our colours are black, red, white and grey.

Files must be supplied in eps, pdf and ai format.

Please display the following information:
Derek Halloway
Account Manager
Suite xxx, 212 Ferrow Lane Melbourne, Victoria 3000
Phone +61 3 5550 1827
Mobile +61 455 016 342
sales@brandvelle-example.com.au
www.brandvelle-example.com.au

```html
<!DOCTYPE html>
<html lang="en">
<head>
<meta charset="utf-8">
<title>Brandvelle Stationery</title>
<link rel="stylesheet" href="https://fonts.googleapis.com/css2?family=Exo+2:wght@400;600;700&display=swap">
<style>
:root{
  --stage:#e6e1d9;
  --paper:#ffffff;
  --red:#d8202a;
  --red-deep:#7e1117;
  --red-bright:#ee3038;
  --ink:#4a4a4a;
  --ink-dark:#2b2b2b;
  --rule:#b9b9b9;
}
*{margin:0;padding:0;box-sizing:border-box}
html,body{width:1200px;height:1024px;overflow:hidden;background:var(--stage);font-family:"Exo 2",sans-serif}
.canvas{position:relative;width:1200px;height:1024px}
.piece{position:absolute;overflow:hidden;box-shadow:0 3px 8px rgba(0,0,0,.28)}
.white{background:var(--paper)}
.red{background:radial-gradient(ellipse at 50% 48%,var(--red-bright) 0%,var(--red) 35%,var(--red-deep) 100%)}
.base-band{position:absolute;left:0;right:0;bottom:0;background:linear-gradient(90deg,var(--red-deep),var(--red) 70%,var(--red-bright))}
.base-rule{position:absolute;left:0;right:0;height:3px;background:var(--rule)}
.brand{display:flex;flex-direction:column;align-items:center;position:absolute}
.brand-dot{border-radius:50%;background:var(--red)}
.white .brand-name{color:var(--ink-dark)}
.red .brand-dot{background:#fff}
.red .brand-name{color:#fff}
.brand-name{font-weight:700;letter-spacing:.5px;text-transform:uppercase;line-height:1}
.contact{position:absolute;color:var(--ink);line-height:1.3}
.contact .sep{display:block;height:.5em}
.contact i{display:inline-block;width:.7em;height:.7em;background:var(--red);border-radius:2px;margin-right:3px;vertical-align:-1px}
.divider{position:absolute;width:1px;background:#ccc}
.url{position:absolute;color:#fff;font-size:10px}
.red .url{left:0;right:0;text-align:center}
.letterhead{left:22px;top:38px;width:386px;height:548px}
.cover{left:422px;top:38px;width:388px;height:548px}
.card-front{left:836px;top:74px;width:346px;height:196px;border-radius:14px}
.card-back{left:823px;top:322px;width:359px;height:204px;border-radius:14px}
.env-front{left:28px;top:617px;width:562px;height:380px}
.env-back{left:612px;top:617px;width:560px;height:380px}
.window{position:absolute;left:28px;top:183px;width:198px;height:72px;border:1px solid #bbb;border-radius:8px;background:linear-gradient(#f4f4f4,#e2e2e2)}
.person{position:absolute;left:200px;top:38px}
.person-name{color:var(--red);font-weight:600;font-size:11px;text-transform:uppercase}
.person-role{color:var(--ink);font-size:9px}
</style>
</head>
<body>
<div class="canvas">

<section class="piece white letterhead">
  <div class="brand" style="left:18px;top:24px">
    <span class="brand-dot" style="width:40px;height:40px;margin-bottom:8px"></span>
    <span class="brand-name" style="font-size:17px">Brandvelle</span>
  </div>
  <span class="divider" style="left:224px;top:22px;height:62px"></span>
  <p class="contact" style="left:232px;top:26px;font-size:8px">
    <i></i>+61 3 5550 1827<br><i></i>+61 455 016 342<br><i></i>sales@brandvelle-example.com.au<br>
    Suite xxx, 212 Ferrow Lane<br>Melbourne, Victoria 3000
  </p>
  <span class="base-rule" style="bottom:46px"></span>
  <div class="base-band" style="height:40px"></div>
  <span class="url" style="right:14px;bottom:14px;font-size:9px">www.brandvelle-example.com.au</span>
</section>

<section class="piece red cover">
  <div class="brand" style="left:0;right:0;top:210px">
    <span class="brand-dot" style="width:56px;height:56px;margin-bottom:18px"></span>
    <span class="brand-name" style="font-size:27px">Brandvelle</span>
  </div>
  <span class="url" style="bottom:20px">www.brandvelle-example.com.au</span>
</section>

<section class="piece white card-front">
  <div class="brand" style="left:16px;top:40px;width:150px">
    <span class="brand-dot" style="width:40px;height:40px;margin-bottom:10px"></span>
    <span class="brand-name" style="font-size:17px">Brandvelle</span>
  </div>
  <span class="divider" style="left:180px;top:34px;height:80px"></span>
  <div class="person">
    <p class="person-name">Derek Halloway</p>
    <p class="person-role">Account Manager</p>
    <p class="contact" style="position:static;font-size:8px;margin-top:6px">
      <i></i>+61 3 5550 1827<br><i></i>+61 455 016 342<br><i></i>sales@brandvelle-example.com.au<br><span class="sep"></span>
      Suite xxx, 212 Ferrow Lane<br>Melbourne, Victoria 3000
    </p>
  </div>
  <span class="base-rule" style="bottom:30px"></span>
  <div class="base-band" style="height:25px"></div>
  <span class="url" style="right:14px;bottom:7px;font-size:9px">www.brandvelle-example.com.au</span>
</section>

<section class="piece red card-back">
  <div class="brand" style="left:0;right:0;top:40px">
    <span class="brand-dot" style="width:44px;height:44px;margin-bottom:14px"></span>
    <span class="brand-name" style="font-size:22px">Brandvelle</span>
  </div>
  <span class="url" style="bottom:22px;font-size:10px">www.brandvelle-example.com.au</span>
</section>

<section class="piece white env-front">
  <div class="brand" style="left:26px;top:36px">
    <span class="brand-dot" style="width:44px;height:44px;margin-bottom:12px"></span>
    <span class="brand-name" style="font-size:19px">Brandvelle</span>
  </div>
  <p class="contact" style="left:362px;top:48px;font-size:11px">
    <i></i>+61 3 5550 1827<br><i></i>+61 455 016 342<br><i></i>sales@brandvelle-example.com.au<br><span class="sep"></span>
    Suite xxx, 212 Ferrow Lane<br>Melbourne, Victoria 3000
  </p>
  <div class="window"></div>
  <span class="base-rule" style="bottom:52px"></span>
  <div class="base-band" style="height:46px"></div>
  <span class="url" style="right:18px;bottom:16px;font-size:12px">www.brandvelle-example.com.au</span>
</section>

<section class="piece red env-back">
  <svg style="position:absolute;left:0;top:0" width="560" height="140">
    <path d="M0 0 L280 120 L560 0" fill="rgba(0,0,0,.08)" stroke="rgba(0,0,0,.25)" stroke-width="1.5"/>
  </svg>
  <div class="brand" style="left:0;right:0;top:14px">
    <span class="brand-dot" style="width:34px;height:34px;margin-bottom:10px"></span>
    <span class="brand-name" style="font-size:13px">Brandvelle</span>
  </div>
  <span class="url" style="bottom:26px;font-size:12px">www.brandvelle-example.com.au</span>
</section>

</div>
</body>
</html>
```